Wilderness Doc & TV personality personal page

I’m a wilderness and EMS emergency physician with particular sub specialties and a TV show. I need a website to highlight my interviews, teachings, etc... I did buy a number of domains for now.
Topics and things I need: CV (or version) me in the media, picture gallery, actually I sort of really like what dr owen barkley, my colleague has setup plus I have tv show and stuff like that. ridgeway healer dot com

Target Market(s)

EMS, education, commercial products...

Industry/Entity Type

Medical And Science

Coding

Coded - Design and coding required

Number of Pages Required

1 page

Font styles to use
Sans Serif

Colors
f37122
9bcb3c
0556a4
a54499

Requirements
Must have
• Links and photos to news articles and things that mention me that I can add in.
Nice to have
• Maybe some snapshots of lecture reviews or patient thank you notes. Accolades so to speak
• I really appreciate how sharp it is. I would love to see Headings that resemble my friend's at ridgeway healer dot com. Home, experience, consulting, lectures, affiliates, contact... those are main subjects... I think media also and that will have the TV show stuff and articles written about me...then maybe at the bottom of main page also have splits for training, research, television, and maybe exploration
Should not have
• The medical symbol with two snakes... that means quack doctor

```html
<!DOCTYPE html>
<html lang="en">
<head>
<meta charset="utf-8">
<title>Dr Owen Barkley — Wilderness &amp; EMS Physician</title>
<link href="https://fonts.googleapis.com/css2?family=Montserrat:ital,wght@0,300;0,400;0,500;0,600;0,700;1,400&family=Outfit:wght@300;600;700&display=swap" rel="stylesheet">
<style>
:root{
  --orange:#f37122;
  --green:#9bcb3c;
  --blue:#0556a4;
  --blue-soft:#7ea6d3;
  --ink:#333333;
  --muted:#6b6b6b;
  --footer:#444444;
  --sheet:#e9e9e9;
  --white:#ffffff;
}
*{box-sizing:border-box;margin:0;padding:0}
html,body{width:1200px;height:3312px;overflow:hidden}
body{background:var(--sheet);font-family:"Montserrat",Arial,sans-serif;color:var(--ink);position:relative}
.abs{position:absolute}
.head{font-family:"Outfit","Montserrat",sans-serif;font-weight:700}
.logo b{color:var(--green);font-weight:700}
.logo{font-family:"Outfit",sans-serif;font-weight:600;color:var(--ink);white-space:nowrap}
.logo-light{color:var(--white)}
.sheet-logo{left:77px;top:52px;font-size:44px}

/* ---------- desktop page ---------- */
.desktop{left:350px;top:64px;width:779px;height:3175px;background:var(--white);overflow:hidden}
.topbar{left:0;top:0;width:779px;height:66px}
.topbar .logo{left:49px;top:18px;font-size:24px}
.nav{left:293px;top:26px;display:flex;gap:15px;font-size:8.5px;color:var(--muted)}
.nav .on{color:var(--blue)}
.search{left:637px;top:23px;width:93px;height:20px;border:1px solid #555;border-radius:10px;font-size:8px;color:#777;padding:4px 10px}
.search svg{position:absolute;right:7px;top:4px}
.hero{left:0;top:66px;width:779px;height:454px;background:linear-gradient(135deg,#2f5b93 0%,#3c6aa0 45%,#23466f 100%)}
.hero-kicker{left:0;width:779px;top:116px;text-align:center;color:var(--white);font-family:"Outfit",sans-serif;font-weight:300;font-size:34px}
.hero-title{left:0;width:779px;top:152px;text-align:center;color:var(--white);font-size:66px;line-height:1}
.hero-title span{color:var(--green)}
.hero-text{left:175px;width:430px;top:238px;text-align:center;color:var(--white);font-size:9.5px;line-height:16px}
.btn{display:flex;align-items:center;justify-content:center;border-radius:14px;font-size:9px;white-space:nowrap}
.btn-solid{background:var(--white);color:var(--ink)}
.btn-line{border:1px solid var(--white);color:var(--white)}
.btn-dark{border:1px solid var(--ink);color:var(--ink)}
.btn-green{border:1px solid var(--blue);color:var(--blue)}
.hero .b1{left:283px;top:347px;width:104px;height:26px}
.hero .b2{left:395px;top:347px;width:101px;height:26px}

.card{background:var(--orange);color:var(--white);text-align:center}
.card .t{position:absolute;left:0;right:0;top:64px;font-size:20px}
.card .s{position:absolute;left:30px;right:30px;top:92px;font-size:9.5px;line-height:15px}
.d-interview{left:49px;top:556px;width:190px;height:190px}
.d-teaching{left:251px;top:556px;width:190px;height:190px}
.d-tv{left:451px;top:556px;width:279px;height:190px}
.play{position:absolute;border-radius:50%;background:var(--white)}
.play::after{content:"";position:absolute;border-left:9px solid var(--orange);border-top:6px solid transparent;border-bottom:6px solid transparent;left:11px;top:8px}

.d-consult-title{left:49px;top:808px;font-size:43px;color:var(--ink)}
.d-consult-text{left:49px;top:880px;width:500px;font-size:9.5px;line-height:18px;color:var(--muted)}
.service{text-align:center}
.service .name{font-size:16px;font-weight:500;line-height:18px;color:var(--ink)}
.service .txt{font-size:9.5px;line-height:18px;color:var(--muted);margin-top:12px}
.svc1{left:46px;top:965px;width:160px}
.svc2{left:281px;top:965px;width:210px}
.svc3{left:567px;top:965px;width:170px}
.vline{width:1px;background:#cfcfcf}

.cv-band{left:0;top:1218px;width:779px;height:101px;background:var(--blue)}
.cv-band .t{left:164px;top:30px;font-size:30px;color:var(--white)}
.cv-band .b{left:510px;top:38px;width:105px;height:26px}

.photo{overflow:hidden}
.g-man{left:0;top:1356px;width:429px;height:501px;background:linear-gradient(160deg,#4d5a6d,#2a3447 60%,#1f2a3d)}
.g-crew{left:441px;top:1356px;width:338px;height:190px;background:linear-gradient(160deg,#b9c3cc,#6d7884 60%,#3d4651)}
.g-side{left:694px;top:1558px;width:85px;height:299px;background:linear-gradient(180deg,#c9b9a4,#5e5a57)}
.g-box{left:233px;top:1558px;width:450px;height:330px;background:var(--green)}
.g-box .t{left:57px;top:58px;font-size:38px;color:var(--ink)}
.g-box .p{left:57px;top:114px;width:350px;font-size:9.5px;line-height:18px;color:var(--blue)}
.g-box .b{left:51px;top:238px;width:106px;height:27px}

.news-title{left:51px;top:1940px;font-size:40px;line-height:44px;color:var(--ink)}
.news-text{left:49px;top:2037px;width:235px;font-size:9.5px;line-height:18px;color:var(--muted)}
.news-btn{left:49px;top:2182px;width:104px;height:27px}
.n1{left:316px;top:1955px;width:203px;height:209px;background:linear-gradient(150deg,#56627a,#2e3b52)}
.n2{left:527px;top:1955px;width:202px;height:209px;background:linear-gradient(180deg,#7f9cc4,#d6dde6 60%,#6a7680)}
.n-cap{font-size:9.5px;line-height:17px;color:var(--muted);width:205px}

.tabs{left:0;top:2276px;width:779px;height:99px;background:var(--blue)}
.tab{position:absolute;top:36px;font-size:20px;color:var(--blue-soft)}
.tab.on{color:var(--white)}
.tabs .vline{position:absolute;top:18px;height:63px;background:rgba(255,255,255,.35)}

.hp-title{left:51px;top:2437px;font-size:40px;color:var(--ink)}
.pt-photo{width:161px;height:160px;background:linear-gradient(160deg,#9a9a9a,#4a4a4a)}
.pt{width:205px}
.pt .n{font-size:16px;color:var(--green)}
.pt .r{font-size:9.5px;font-style:italic;color:var(--muted);margin-top:3px}
.pt .q{font-size:9.5px;line-height:18px;color:var(--muted);margin-top:12px}
.pt .stars{margin-top:8px;font-size:11px;color:#f5c400;letter-spacing:1px}
.pt .stars i{font-style:normal;color:var(--green);font-size:9px;margin-left:6px}
.faded{opacity:.25}

.news-band{left:0;top:2758px;width:779px;height:119px;background:var(--orange)}
.news-band .t{left:49px;top:50px;font-size:29px;color:var(--white)}
.field{border:1px solid var(--white);border-radius:14px;color:var(--white);font-size:9px;padding:0 12px;display:flex;align-items:center}
.news-band .field{left:417px;top:50px;width:246px;height:27px}

.footer{left:0;top:2877px;width:779px;height:298px;background:var(--footer);color:#e8e8e8}
.footer h4{position:absolute;font-weight:500;font-size:15px;color:var(--white)}
.flinks{font-size:7.5px;line-height:18px}
.fcontact{font-size:7.5px;line-height:18px}
.social{width:11px;height:11px;border-radius:50%;display:inline-block}
.s-blue{background:#3b5fa8}.s-pink{background:#c9397f}
.footer .logo{font-size:22px}
.fabout{font-size:9.5px;line-height:18px}
.fline{height:1px;background:#5a5a5a}
.copy{font-size:9.5px}

/* ---------- mobile page ---------- */
.mobile{left:80px;top:148px;width:203px;height:2269px;background:var(--white);overflow:hidden}
.m-bar .logo{left:17px;top:11px;font-size:11px}
.m-hero{left:0;top:34px;width:203px;height:327px;background:linear-gradient(135deg,#2f5b93,#3c6aa0 45%,#23466f)}
.m-kicker{left:0;width:203px;top:100px;text-align:center;color:var(--white);font-family:"Outfit",sans-serif;font-weight:300;font-size:14px}
.m-title{left:0;width:203px;top:117px;text-align:center;color:var(--white);font-size:24px}
.m-title span{color:var(--green)}
.m-text{left:30px;width:143px;top:150px;text-align:center;color:var(--white);font-size:5.5px;line-height:10px}
.m-hero .btn{font-size:5.5px;height:14px;border-radius:7px}
.m-card .t{top:24px;font-size:10px}
.m-card .s{top:38px;left:8px;right:8px;font-size:5px;line-height:8px}
.tiny{font-size:5.5px;line-height:12px;color:var(--muted)}
.m-h{font-size:16px;color:var(--ink)}
</style>
</head>
<body>

<div class="abs logo sheet-logo"><b>Logo</b> Here</div>

<!-- ================= MOBILE ================= -->
<section class="abs mobile" aria-label="Mobile layout">
  <div class="m-bar">
    <div class="abs logo"><b>Logo</b> Here</div>
    <svg class="abs" style="left:163px;top:12px" width="26" height="10" viewBox="0 0 26 10"><path d="M0 1h10M0 5h10M0 9h10" stroke="#333" stroke-width="1.6"/><circle cx="19" cy="4.5" r="3.2" fill="none" stroke="#333" stroke-width="1.3"/><path d="M21.3 6.8l2.5 2.5" stroke="#333" stroke-width="1.3"/></svg>
  </div>
  <div class="abs m-hero" role="img" aria-label="Medical helicopter crew loading a patient, blue tinted">
    <div class="abs m-kicker">Lorem Ipsum</div>
    <div class="abs head m-title">Dolor Sit <span>Amet</span></div>
    <div class="abs m-text">Lorem Ipsum Is Simply Dummy Text Of The Printing And Typesetting Industry. Lorem Ipsum Has Been The Industry's Standard Dummy Text.</div>
    <div class="abs btn btn-solid" style="left:35px;top:209px;width:64px">Text Here</div>
    <div class="abs btn btn-line" style="left:104px;top:209px;width:64px">Text Here</div>
  </div>

  <div class="abs card m-card" style="left:17px;top:381px;width:83px;height:84px" role="img" aria-label="Interview photo, orange tint"><div class="t head">Interview</div><div class="s">Lorem Ipsum Is Simply Dummy</div></div>
  <div class="abs card m-card" style="left:105px;top:381px;width:83px;height:84px" role="img" aria-label="Teaching photo, orange tint"><div class="t head">Teaching</div><div class="s">Lorem Ipsum Is Simply Dummy</div></div>
  <div class="abs card m-card" style="left:17px;top:469px;width:171px;height:117px" role="img" aria-label="TV show helicopter scene, orange tint"><div class="t head" style="top:42px">TV Show</div><div class="play" style="left:78px;top:58px;width:15px;height:15px;transform:scale(.5);transform-origin:0 0;width:30px;height:30px"></div></div>

  <div class="abs head m-h" style="left:17px;top:624px">Consulting</div>
  <div class="abs tiny" style="left:17px;top:652px;width:168px">Lorem Ipsum Dolor Sit Amet, Consectetur Adipiscing Elit, Sed Do Eiusmod Tempor Incididunt Ut Labore Et Dolore Magna Aliqua. Ut Enim Ad Minim Veniam, Quis Nostrud Exercitation Ullamco Laboris Nisi Ut Aliquip Ex Ea Commodo Consequat.</div>
  <svg class="abs" style="left:37px;top:746px" width="32" height="34" viewBox="0 0 64 68" fill="none" stroke="#f37122" stroke-width="2.5"><circle cx="26" cy="18" r="12"/><path d="M4 62c0-14 10-22 22-22s18 6 20 10"/><circle cx="46" cy="50" r="12"/><path d="M46 44v12M40 50h12"/></svg>
  <div class="abs" style="left:20px;top:792px;width:70px;text-align:center;font-size:7px;color:var(--ink)">Teaching</div>
  <div class="abs tiny" style="left:15px;top:811px;width:76px;text-align:center;line-height:11px">Lorem Ipsum Dolor Sit Amet, Consectetur Adipiscing Elit, Sed Do Eiusmod</div>
  <div class="abs vline" style="left:102px;top:775px;height:60px"></div>
  <svg class="abs" style="left:154px;top:746px" width="30" height="34" viewBox="0 0 64 68" fill="none" stroke="#0556a4" stroke-width="2.5"><path d="M20 58V34a12 12 0 0 1 24 0v24M14 58h36v6H14z"/><path d="M32 4v8M12 14l5 5M52 14l-5 5M4 32h7M53 32h7"/><circle cx="32" cy="40" r="4"/></svg>
  <div class="abs" style="left:114px;top:788px;width:100px;font-size:6.5px;line-height:8px;color:var(--ink);text-align:center">MedicoLegal Case Review And Trial Consulting</div>
  <div class="abs tiny" style="left:120px;top:814px;width:80px;text-align:center;line-height:11px">Lorem Ipsum Dolor Sit Amet, Consectetur Adipiscing Elit, Sed Eiusmod</div>

  <div class="abs" style="left:0;top:905px;width:203px;height:123px;background:var(--blue)">
    <div class="abs head" style="left:0;width:203px;top:37px;text-align:center;color:#fff;font-size:16px;line-height:18px">Take A Look At My<br>CV</div>
    <div class="abs btn btn-line" style="left:69px;top:78px;width:65px;height:14px;font-size:5.5px">View CV</div>
  </div>

  <div class="abs" style="left:0;top:1048px;width:116px;height:157px;background:linear-gradient(160deg,#4d5a6d,#1f2a3d)" role="img" aria-label="Paramedic in uniform"></div>
  <div class="abs" style="left:121px;top:1048px;width:82px;height:52px;background:linear-gradient(160deg,#b9c3cc,#3d4651)" role="img" aria-label="Crew moving a stretcher from an ambulance"></div>
  <div class="abs" style="left:192px;top:1110px;width:11px;height:90px;background:linear-gradient(180deg,#c9b9a4,#5e5a57)" role="img" aria-label="Gallery photo"></div>
  <div class="abs" style="left:54px;top:1104px;width:134px;height:133px;background:var(--green)">
    <div class="abs head" style="left:19px;top:19px;font-size:14px;color:var(--ink)">Image Gallery</div>
    <div class="abs" style="left:19px;top:42px;width:100px;font-size:5px;line-height:10px;color:var(--blue)">Lorem Ipsum Dolor Sit Amet, Consectetur Adipiscing Elit, Sed Do Eiusmod Tempor Incididunt Ut Labore Et Dolore Magna Aliqua. Ut Enim</div>
    <div class="abs btn btn-green" style="left:19px;top:109px;width:67px;height:14px;font-size:5.5px">Text Here</div>
  </div>

  <div class="abs head" style="left:17px;top:1263px;font-size:15px;line-height:17px;color:var(--ink)">Recent<br>News</div>
  <div class="abs tiny" style="left:17px;top:1308px;width:168px">Lorem Ipsum Dolor Sit Amet, Consectetur Adipiscing Elit, Sed Do Eiusmod Tempor Incididunt Ut Labore Et Dolore Magna Aliqua. Ut Enim Ad Minim Veniam, Quis Nostrud Exercitation Ullamco Laboris Nisi Ut Aliquip Ex Ea Commodo Consequat.</div>
  <div class="abs" style="left:17px;top:1402px;width:122px;height:126px;background:linear-gradient(150deg,#56627a,#2e3b52)" role="img" aria-label="Medic tending a patient on a stretcher"></div>
  <div class="abs" style="left:143px;top:1402px;width:60px;height:126px;background:linear-gradient(180deg,#7f9cc4,#d6dde6 60%,#6a7680)" role="img" aria-label="Ambulance parked outside a building"></div>
  <div class="abs tiny" style="left:17px;top:1532px;width:120px;line-height:11px">Lorem Ipsum Dolor Sit Amet, Consectetur Adipiscing Elit.</div>
  <div class="abs tiny" style="left:143px;top:1532px;width:120px;line-height:11px">Lorem Ipsum Dolor Sit Amet, Consectetur Adipiscing</div>

  <div class="abs" style="left:0;top:1594px;width:203px;height:52px;background:var(--blue)">
    <div class="abs head" style="left:17px;top:20px;font-size:9px;color:var(--blue-soft)">Training</div>
    <div class="abs" style="left:68px;top:16px;width:1px;height:20px;background:rgba(255,255,255,.35)"></div>
    <div class="abs head" style="left:80px;top:20px;font-size:9px;color:#fff">Reasearch</div>
    <div class="abs" style="left:142px;top:16px;width:1px;height:20px;background:rgba(255,255,255,.35)"></div>
    <div class="abs head" style="left:153px;top:20px;font-size:9px;color:var(--blue-soft);white-space:nowrap">Television</div>
  </div>

  <div class="abs head" style="left:15px;top:1690px;font-size:15px;color:var(--ink)">Happy Patient</div>
  <div class="abs" style="left:15px;top:1717px;width:62px;height:62px;background:linear-gradient(160deg,#9a9a9a,#4a4a4a)" role="img" aria-label="Patient portrait, black and white"></div>
  <div class="abs" style="left:87px;top:1719px;font-size:7px;color:var(--green)">Marcus Hale</div>
  <div class="abs" style="left:87px;top:1730px;width:90px;font-size:4.5px;line-height:9px;color:var(--muted)"><i>Lorem Ipsum Dolor Sit Amet.</i><br>Lorem Ipsum Dolor Sit Amet, Consectetur Adipiscing Elit, Sed Do<br><span style="color:#f5c400">★★★★★</span> <span style="color:var(--green)">5.0</span></div>
  <div class="abs" style="left:181px;top:1717px;width:22px;height:62px;background:linear-gradient(160deg,#bdbdbd,#777)" role="img" aria-label="Patient portrait"></div>

  <div class="abs" style="left:0;top:1821px;width:203px;height:129px;background:var(--orange)">
    <div class="abs head" style="left:17px;top:37px;font-size:14px;line-height:17px;color:#fff">Subscribe Our<br>Newsletter</div>
    <div class="abs field" style="left:17px;top:79px;width:124px;height:15px;font-size:5.5px;border-radius:8px">Email Address</div>
    <svg class="abs" style="left:152px;top:79px" width="16" height="14" viewBox="0 0 26 22" fill="none" stroke="#fff" stroke-width="1.4"><path d="M1 10L25 1 19 21 12 13z"/><path d="M12 13L25 1"/></svg>
  </div>

  <div class="abs" style="left:0;top:1950px;width:203px;height:319px;background:var(--footer);color:#e8e8e8">
    <div class="abs logo logo-light" style="left:17px;top:27px;font-size:10px">Logo Here</div>
    <div class="abs" style="left:17px;top:60px;width:170px;font-size:5px;line-height:11px">Lorem Ipsum Dolor Sit Amet, Consectetur Adipiscing Elit, Sed Do Eiusmod Tempor Incididunt Ut Labore Et Dolore Magna Aliqua. Ut</div>
    <div class="abs" style="left:17px;top:122px;font-size:6.5px;color:#fff">Quick Links</div>
    <div class="abs" style="left:17px;top:146px;font-size:5px;line-height:15.5px">Home<br>Services<br>Interviews<br>Our Galleries<br>Contact Us</div>
    <div class="abs" style="left:81px;top:134px;width:1px;height:84px;background:#5a5a5a"></div>
    <div class="abs" style="left:100px;top:122px;font-size:6.5px;color:#fff">Contact Us</div>
    <svg class="abs" style="left:100px;top:145px" width="7" height="9" viewBox="0 0 10 13" fill="none" stroke="#fff" stroke-width="1.1"><path d="M5 12S1 7 1 4.5a4 4 0 0 1 8 0C9 7 5 12 5 12z"/><circle cx="5" cy="4.5" r="1.4"/></svg>
    <div class="abs" style="left:118px;top:144px;width:80px;font-size:5px;line-height:15px">Lorem Ipsum Dolor Sit Amet, Consectetur Adipiscing</div>
    <svg class="abs" style="left:100px;top:202px" width="9" height="9" viewBox="0 0 12 12" fill="none" stroke="#fff" stroke-width="1"><circle cx="6" cy="6" r="5.3"/><path d="M4 3.5l1 1.3-.6.8a4 4 0 0 0 2 2l.8-.6 1.3 1-.7 1c-2.2 0-4.5-2.3-4.5-4.5z"/></svg>
    <div class="abs" style="left:118px;top:202px;font-size:5px">021-5580-2214-0</div>
    <span class="abs social s-blue" style="left:100px;top:220px;width:9px;height:9px"></span>
    <span class="abs social s-pink" style="left:112px;top:220px;width:9px;height:9px"></span>
    <div class="abs" style="right:17px;top:295px;font-size:5.5px">Copyright © 2019. All Rights Reserved.</div>
  </div>
</section>

<!-- ================= DESKTOP ================= -->
<section class="abs desktop" aria-label="Desktop layout">
  <header class="abs topbar">
    <div class="abs logo"><b>Logo</b> Here</div>
    <nav class="abs nav"><span class="on">Home</span><span>Experience</span><span>Consulting</span><span>Lectures</span><span>Affiliates</span><span>Media</span><span>Contact</span></nav>
    <div class="abs search">Search<svg width="11" height="11" viewBox="0 0 11 11"><circle cx="4.5" cy="4.5" r="3.6" fill="none" stroke="#333" stroke-width="1.2"/><path d="M7.2 7.2l3 3" stroke="#333" stroke-width="1.2"/></svg></div>
  </header>

  <div class="abs hero" role="img" aria-label="Air ambulance crew loading a patient beside a helicopter, blue tinted">
    <div class="abs hero-kicker">Lorem Ipsum</div>
    <div class="abs head hero-title">Dolor Sit <span>Amet</span></div>
    <p class="abs hero-text">Lorem Ipsum Is Simply Dummy Text Of The Printing And Typesetting Industry. Lorem Ipsum Has Been The Industry's Standard Dummy Text.</p>
    <div class="abs btn btn-solid b1">Text Here</div>
    <div class="abs btn btn-line b2">Text Here</div>
  </div>

  <div class="abs card d-interview" role="img" aria-label="Interview photo, orange tint"><div class="t head">Interview</div><div class="s">Lorem Ipsum Is Simply Dummy Text Of The</div></div>
  <div class="abs card d-teaching" role="img" aria-label="Teaching photo, orange tint"><div class="t head">Teaching</div><div class="s">Lorem Ipsum Is Simply Dummy Text Of The</div></div>
  <div class="abs card d-tv" role="img" aria-label="TV show, crew beside a rescue helicopter, orange tint"><div class="t head">TV Show</div><div class="play" style="left:125px;top:98px;width:30px;height:30px"></div></div>

  <h2 class="abs head d-consult-title">Consulting</h2>
  <p class="abs d-consult-text">Lorem Ipsum Dolor Sit Amet, Consectetur Adipiscing Elit, Sed Do Eiusmod Tempor Incididunt Ut Labore Et Dolore Magna Aliqua. Ut Enim Ad Minim Veniam, Quis Nostrud Exercitation Ullamco Laboris Nisi Ut Aliquip Ex Ea Commodo Consequat.</p>

  <svg class="abs" style="left:94px;top:966px" width="66" height="70" viewBox="0 0 64 68" fill="none" stroke="#f37122" stroke-width="2"><circle cx="26" cy="18" r="12"/><path d="M18 14c4-4 12-4 16 0"/><path d="M4 64c0-14 10-24 22-24 7 0 12 3 16 7"/><circle cx="46" cy="50" r="12"/><path d="M46 43v14M39 50h14"/></svg>
  <svg class="abs" style="left:350px;top:960px" width="70" height="72" viewBox="0 0 64 68" fill="none" stroke="#0556a4" stroke-width="2"><path d="M20 56V34a12 12 0 0 1 24 0v22M12 56h40v8H12z"/><path d="M32 2v9M11 12l6 6M53 12l-6 6M2 32h9M53 32h9"/><rect x="28" y="32" width="8" height="12" rx="4"/></svg>
  <svg class="abs" style="left:617px;top:966px" width="70" height="68" viewBox="0 0 70 68" fill="none" stroke="#9bcb3c" stroke-width="2"><circle cx="35" cy="16" r="9"/><path d="M20 66V40c0-8 7-13 15-13s15 5 15 13v26M35 27v39"/><circle cx="14" cy="14" r="7"/><path d="M2 50V34c0-6 5-10 12-10 3 0 6 1 8 3"/><circle cx="56" cy="14" r="7"/><path d="M68 50V34c0-6-5-10-12-10-3 0-6 1-8 3"/></svg>

  <div class="abs service svc1" style="top:1055px"><div class="name">Teaching</div><div class="txt">Lorem Ipsum Dolor Sit Amet, Consectetur Adipiscing Elit, Sed Do Eiusmod</div></div>
  <div class="abs vline" style="left:239px;top:1002px;height:121px"></div>
  <div class="abs service svc2" style="top:1053px"><div class="name">MedicoLegal Case Review<br>And Trial Consulting</div><div class="txt">Lorem Ipsum Dolor Sit Amet, Consectetur Adipiscing Elit, Sed Do Eiusmod</div></div>
  <div class="abs vline" style="left:538px;top:1002px;height:121px"></div>
  <div class="abs service svc3" style="top:1055px"><div class="name">Travel Expedition</div><div class="txt">Lorem Ipsum Dolor Sit Amet, Consectetur Adipiscing Elit, Sed Do Eiusmod</div></div>

  <div class="abs cv-band">
    <div class="abs head t">Take A Look At My CV</div>
    <div class="abs btn btn-line b">View CV</div>
  </div>

  <div class="abs photo g-man" role="img" aria-label="Smiling paramedic in navy uniform with stethoscope"></div>
  <div class="abs photo g-crew" role="img" aria-label="Crew moving a patient on a stretcher from an ambulance"></div>
  <div class="abs photo g-side" role="img" aria-label="Gallery photo, partially shown"></div>
  <div class="abs g-box">
    <h2 class="abs head t">Image Gallery</h2>
    <p class="abs p">Lorem Ipsum Dolor Sit Amet, Consectetur Adipiscing Elit, Sed Do Eiusmod Tempor Incididunt Ut Labore Et Dolore Magna Aliqua. Ut Enim Ad Minim Veniam, Quis Nostrud Exercitation Ullamco Laboris Nisi Ut Aliquip Ex Ea Commodo Consequat. Duis Aute Irure Dolor In Reprehenderit In Voluptate</p>
    <div class="abs btn btn-green b">Text Here</div>
  </div>

  <h2 class="abs head news-title">Recent<br>News</h2>
  <p class="abs news-text">Lorem Ipsum Dolor Sit Amet, Consectetur Adipiscing Elit, Sed Do Eiusmod Tempor Incididunt Ut Labore Et Dolore Magna Aliqua. Ut Enim Ad Minim Veniam, Quis Nostrud Exercitation Ullamco Laboris Nisi Ut Aliquip Ex Ea Commodo Consequat.</p>
  <div class="abs btn btn-dark news-btn">Text Here</div>
  <div class="abs photo n1" role="img" aria-label="Medic tending a patient on a stretcher inside an ambulance"></div>
  <div class="abs photo n2" role="img" aria-label="Ambulance parked outside a brick building"></div>
  <p class="abs n-cap" style="left:316px;top:2175px">Lorem Ipsum Dolor Sit Amet, Consectetur Adipiscing Elit.</p>
  <p class="abs n-cap" style="left:527px;top:2175px">Lorem Ipsum Dolor Sit Amet, Consectetur Adipiscing Elit.</p>

  <nav class="abs tabs">
    <span class="tab head" style="left:51px">Training</span>
    <span class="vline" style="left:181px"></span>
    <span class="tab head on" style="left:233px">Reasearch</span>
    <span class="vline" style="left:377px"></span>
    <span class="tab head" style="left:431px">Television</span>
    <span class="vline" style="left:573px"></span>
    <span class="tab head" style="left:627px">Exploration</span>
  </nav>

  <h2 class="abs head hp-title">Happy Patients</h2>
  <div class="abs pt-photo" style="left:51px;top:2532px" role="img" aria-label="Patient portrait, black and white"></div>
  <div class="abs pt" style="left:235px;top:2544px">
    <div class="n">Marcus Hale</div>
    <div class="r">Lorem Ipsum Dolor Sit Amet.</div>
    <div class="q">Lorem Ipsum Dolor Sit Amet, Consectetur Adipiscing Elit, Sed Do Eiusmod Tempor Incididunt Ut Labore Et Dolore Magna Aliqua.</div>
    <div class="stars">★★★★★<i>5.0</i></div>
  </div>
  <div class="abs pt-photo" style="left:473px;top:2532px" role="img" aria-label="Patient portrait, black and white"></div>
  <div class="abs pt faded" style="left:657px;top:2544px">
    <div class="n">Marcus Hale</div>
    <div class="r">Lorem Ipsum Dolor Sit Amet.</div>
    <div class="q">Lorem Ipsum Dolor Sit Amet, Consectetur Adipiscing Elit, Sed Do Eiusmod Tempor Incididunt Ut Labore Et Dolore Magna Aliqua.</div>
    <div class="stars">★★★★★<i>5.0</i></div>
  </div>

  <div class="abs news-band">
    <h2 class="abs head t">Subscribe Our Newsletter</h2>
    <div class="abs field">Email Address</div>
    <svg class="abs" style="left:675px;top:52px" width="26" height="22" viewBox="0 0 26 22" fill="none" stroke="#fff" stroke-width="1.4"><path d="M1 10L25 1 19 21 12 13z"/><path d="M12 13L25 1"/></svg>
  </div>

  <footer class="abs footer">
    <h4 style="left:50px;top:55px">Quick Links</h4>
    <div class="abs flinks" style="left:50px;top:92px">Home<br>Services<br>Interviews<br>Our Galleries<br>Contact Us</div>
    <h4 style="left:210px;top:55px">Contact Us</h4>
    <svg class="abs" style="left:210px;top:94px" width="10" height="13" viewBox="0 0 10 13" fill="none" stroke="#fff" stroke-width="1.1"><path d="M5 12S1 7 1 4.5a4 4 0 0 1 8 0C9 7 5 12 5 12z"/><circle cx="5" cy="4.5" r="1.4"/></svg>
    <div class="abs fcontact" style="left:228px;top:92px;width:170px">Lorem Ipsum Dolor Sit Amet, Consectetur Adipiscing Elit, Sed Do Eiusmod</div>
    <svg class="abs" style="left:210px;top:142px" width="12" height="12" viewBox="0 0 12 12" fill="none" stroke="#fff" stroke-width="1"><circle cx="6" cy="6" r="5.3"/><path d="M4 3.5l1 1.3-.6.8a4 4 0 0 0 2 2l.8-.6 1.3 1-.7 1c-2.2 0-4.5-2.3-4.5-4.5z"/></svg>
    <div class="abs fcontact" style="left:228px;top:139px">021-5580-2214-0</div>
    <span class="abs social s-blue" style="left:210px;top:164px"></span>
    <span class="abs social s-pink" style="left:228px;top:164px"></span>
    <div class="abs fline" style="left:469px;top:62px;width:1px;height:131px"></div>
    <div class="abs logo logo-light" style="left:575px;top:53px"><span>Logo</span> Here</div>
    <p class="abs fabout" style="left:575px;top:91px;width:160px">Lorem Ipsum Dolor Sit Amet, Consectetur Adipiscing Elit, Sed Do Eiusmod Tempor Incididunt Ut Labore Et Dolore Magna Aliqua. Ut</p>
    <div class="abs fline" style="left:0;top:253px;width:779px"></div>
    <div class="abs copy" style="right:49px;top:275px">Copyright © 2019. All Rights Reserved.</div>
  </footer>
</section>

</body>
</html>
```